Redesign and move to Wordpress for corvandel.com

Our website needs a redesign and at the same time we are moving it to Wordpress. Please help us with a new digital professional look and feel.

We are an Australian Software Engineering company specialising in advanced software development using in A.I., PLatform Engineering, Integration and Cloud. See the current corvandel.com for more information about us.

```html
<!DOCTYPE html>
<html lang="en">
<head>
<meta charset="utf-8">
<title>Corvandel – Reliable Smart Software Engineering</title>
<link href="https://fonts.googleapis.com/css2?family=Audiowide&family=Poppins:wght@300;400;500;600&display=swap" rel="stylesheet">
<style>
:root{
  --teal:#17a5a0;
  --teal-light:#2bbdb6;
  --blue:#1d5fa8;
  --navy:#0f3569;
  --ink:#1c1c1c;
  --muted:#555;
  --mint:#f1fbfb;
  --white:#fff;
  --grad:linear-gradient(90deg,var(--teal) 0%,var(--blue) 100%);
}
*{box-sizing:border-box;margin:0;padding:0}
html,body{width:1200px;height:4464px;overflow:hidden}
body{font-family:"Poppins",sans-serif;color:var(--ink);background:var(--white);position:relative}
.abs{position:absolute}
.display{font-family:"Audiowide",sans-serif;font-weight:400}
.btn{display:inline-flex;align-items:center;justify-content:center;background:var(--grad);color:var(--white);border-radius:4px 12px 4px 12px;font-family:"Poppins",sans-serif;box-shadow:0 3px 6px rgba(0,0,0,.18)}

/* header */
.site-header{left:0;top:0;width:1200px;height:135px;background:var(--grad)}
.brand{display:flex;align-items:center;gap:18px;color:var(--white);font-size:40px;letter-spacing:2px;font-weight:300}
.brand-mark{width:44px;height:44px;border:3px solid var(--white)}
.site-header .brand{left:66px;top:40px}
.search{left:812px;top:26px;width:174px;height:30px;border:2px solid var(--white);border-radius:16px;color:var(--white);font-size:13px;padding:5px 14px}
.search svg{position:absolute;right:12px;top:5px}
.header-phone{left:1010px;top:26px;display:flex;align-items:center;gap:10px;color:var(--white);font-size:14px}
.phone-box{width:28px;height:28px;border:2px solid var(--white);border-radius:6px;display:flex;align-items:center;justify-content:center}
.nav{left:690px;top:86px;display:flex;gap:32px;align-items:center;color:var(--white);font-size:14px}
.nav .active{border-bottom:2px solid var(--white);padding-bottom:2px}
.nav .contact{background:var(--white);color:var(--blue);padding:4px 16px;border-radius:2px}

/* hero */
.hero{left:0;top:135px;width:1200px;height:517px;background:#02060a;overflow:hidden}
.hero-art{left:0;top:0;width:600px;height:517px;background:radial-gradient(ellipse at 35% 45%,#1bc7d4 0%,#0b5d73 35%,#03161f 70%,#02060a 100%)}
.hero-title{left:500px;top:100px;width:600px;text-align:center;color:var(--white)}
.hero-title .small{font-size:40px;letter-spacing:3px}
.hero-title .big{font-size:68px;line-height:84px;letter-spacing:3px}
.hero .btn{left:708px;top:352px;width:188px;height:48px;font-size:19px}

/* section heads */
.kicker{width:1200px;text-align:center;color:var(--blue);font-size:16px;display:flex;justify-content:center;align-items:center;gap:6px}
.kicker::before,.kicker::after{content:"";width:40px;height:2px;background:var(--teal)}
.sec-title{width:1200px;text-align:center;color:var(--teal);font-size:40px;letter-spacing:2px}

/* services */
.service{width:246px;height:231px;overflow:hidden;box-shadow:0 3px 8px rgba(0,0,0,.2);border-radius:2px}
.service .photo{position:absolute;left:0;top:0;width:100%;height:100%}
.service .cap{position:absolute;left:0;bottom:0;width:100%;height:70px;background:linear-gradient(90deg,rgba(23,165,160,.95),rgba(29,95,168,.95));color:var(--white);font-family:"Audiowide",sans-serif;font-size:14px;letter-spacing:1px;display:flex;align-items:center;justify-content:center;text-align:center;line-height:16px;padding:0 10px}
.service.featured{background:var(--navy);color:var(--white);text-align:center;padding:48px 16px 0}
.service.featured h3{font-family:"Audiowide",sans-serif;font-weight:400;font-size:15px;letter-spacing:1px;line-height:18px}
.service.featured p{font-size:12.5px;line-height:16px;margin-top:14px;text-align:justify}
.service.featured .btn{margin-top:16px;padding:4px 16px;font-size:12px;border-radius:12px;background:var(--teal)}

/* about */
.about{left:0;top:1396px;width:1200px;height:456px;background:var(--mint)}
.about .kicker2{left:138px;top:80px;color:var(--blue);font-size:16px;display:flex;align-items:center;gap:10px}
.about .kicker2::after{content:"";width:42px;height:2px;background:var(--teal)}
.about h2{left:138px;top:98px;color:var(--teal);font-size:40px;letter-spacing:2px}
.about p{left:138px;top:150px;width:472px;font-size:13.5px;line-height:23px;text-align:justify;color:#333}
.about .btn{left:143px;top:316px;width:104px;height:32px;font-size:13px}
.about-photo{left:668px;top:36px;width:407px;height:380px;border-radius:0 0 80px 0;background:linear-gradient(135deg,#6d6d6a 0%,#3c3d3a 45%,#8a8885 100%)}

/* newsletter */
.newsletter{left:0;top:1855px;width:1200px;height:443px;background:linear-gradient(180deg,#d7d7d7 0%,#bfc3c6 60%,#9aa3aa 100%)}
.newsletter h2{left:0;top:50px;width:1200px;text-align:center;font-size:66px;font-weight:400;line-height:80px;color:#111}
.newsletter .sub{left:0;top:243px;width:1200px;text-align:center;font-size:27px;color:#111}
.newsletter .field{left:192px;top:320px;width:670px;height:52px;background:var(--white);font-size:17px;color:#666;padding:14px 22px}
.newsletter .submit{left:862px;top:320px;width:164px;height:52px;background:var(--teal-light);color:var(--white);font-size:16px;display:flex;align-items:center;justify-content:center}

/* blog */
.blog{left:0;top:2298px;width:1200px;height:780px;background:var(--mint)}
.post{background:var(--white);box-shadow:0 3px 10px rgba(0,0,0,.12)}
.post .thumb{width:100%}
.post .body{padding:14px 28px}
.post .date{font-size:13px;color:#333}
.post h3{font-weight:400;color:var(--blue);font-size:17px;line-height:23px;margin-top:12px}
.post p{font-size:13px;line-height:18px;color:#333;margin-top:10px}
.post .btn{margin-top:12px;font-size:11px;padding:3px 10px;border-radius:4px 10px 4px 10px}
.post.main h3{color:var(--teal);font-size:20px;line-height:26px;text-decoration:underline}
.post.main p{font-size:15px;line-height:20px}
.blog .more{left:532px;top:702px;width:134px;height:38px;font-size:17px}

/* clients */
.client{top:3161px;width:183px;height:184px;background:var(--white);box-shadow:0 3px 10px rgba(0,0,0,.14);display:flex;align-items:center;justify-content:center;font-size:26px;font-weight:600;color:#1c1c1c}

/* contact */
.contact-lead{left:0;top:3600px;width:1200px;text-align:center;font-size:19px;color:#222}
.input{background:var(--white);box-shadow:0 2px 8px rgba(0,0,0,.14);color:#aaa;font-size:15px;padding:14px 12px}
.contact-submit{left:102px;top:3931px;width:98px;height:33px;font-size:15px}
.map{left:647px;top:3659px;width:412px;height:269px;background:linear-gradient(135deg,#eef0f3 0%,#e2e6ea 50%,#d6dce2 100%);border-radius:0 0 40px 40px;box-shadow:0 2px 6px rgba(0,0,0,.1)}

/* footer */
.footer{left:0;top:4014px;width:1200px;height:450px;background:linear-gradient(90deg,#17a9a2 0%,#1a8ea5 45%,#1d5fa8 100%);border-top:6px solid #8fd9d6;color:var(--white)}
.footer .brand{left:118px;top:172px}
.social{top:236px;width:38px;height:38px;border-radius:50%;background:var(--white)}
.footer h4{font-size:20px;font-weight:600;letter-spacing:.5px}
.footer .links{left:506px;top:176px;font-size:16px;line-height:33px;list-style:none}
.footer .links li::before{content:"›";margin-right:14px;opacity:.7}
.contact-row{display:flex;align-items:center;gap:14px;font-size:16px;line-height:25px}
.icon-circle{width:36px;height:36px;border-radius:50%;background:var(--white);display:flex;align-items:center;justify-content:center;flex:none}
.footer .rule{left:66px;top:364px;width:1068px;height:1px;background:rgba(255,255,255,.6)}
.footer .copy{left:0;top:390px;width:1200px;text-align:center;font-size:14px}
</style>
</head>
<body>

<header class="site-header abs">
  <div class="brand abs"><span class="brand-mark"></span><span>corvandel</span></div>
  <div class="search abs">Search
    <svg width="18" height="18" viewBox="0 0 18 18" fill="none" stroke="#fff" stroke-width="2"><circle cx="7.5" cy="7.5" r="5.5"/><path d="M12 12l4.5 4.5"/></svg>
  </div>
  <div class="header-phone abs">
    <span class="phone-box"><svg width="14" height="14" viewBox="0 0 24 24" fill="#fff"><path d="M6.6 10.8a15 15 0 006.6 6.6l2.2-2.2c.3-.3.7-.4 1-.2 1.1.4 2.3.6 3.6.6.6 0 1 .4 1 1V20c0 .6-.4 1-1 1A17 17 0 013 4c0-.6.4-1 1-1h3.5c.6 0 1 .4 1 1 0 1.3.2 2.5.6 3.6.1.3 0 .7-.2 1z"/></svg></span>
    1800 555 019
  </div>
  <nav class="nav abs">
    <span class="active">Home</span><span>About US</span><span>Services</span><span>Blog</span><span class="contact">Contact Us</span>
  </nav>
</header>

<section class="hero abs">
  <div class="hero-art abs" role="img" aria-label="Glowing teal circuit board with server icons"></div>
  <div class="hero-title abs display">
    <div class="small">Reliable Smart</div>
    <div class="big">Software<br>Engineering</div>
  </div>
  <span class="btn abs">Know More</span>
</section>

<div class="kicker abs" style="top:724px">What We Do</div>
<h2 class="sec-title display abs" style="top:742px">Our Services</h2>

<div class="service featured abs" style="left:75px;top:850px">
  <h3>Enterprise Systems Integration</h3>
  <p>Enterprise systems integration is the process of connecting various IT systems, applications,</p>
  <span class="btn">View More</span>
</div>
<div class="service abs" style="left:342px;top:850px"><div class="photo" role="img" aria-label="Hands typing on a laptop with floating network icons" style="background:linear-gradient(160deg,#4d6f8a,#1f3347)"></div><div class="cap">Microservices</div></div>
<div class="service abs" style="left:610px;top:850px"><div class="photo" role="img" aria-label="Developer working at a desk lamp-lit laptop" style="background:linear-gradient(160deg,#77736c,#2b2a28)"></div><div class="cap">Platform Engineering</div></div>
<div class="service abs" style="left:877px;top:850px"><div class="photo" role="img" aria-label="Monitor showing a chat assistant interface" style="background:linear-gradient(160deg,#5b6a74,#161c22)"></div><div class="cap">Conversational AI</div></div>

<div class="service abs" style="left:75px;top:1101px"><div class="photo" role="img" aria-label="Cloud of connected integration icons" style="background:linear-gradient(160deg,#3e8c86,#0e2a2b)"></div><div class="cap">Integration Platform as a Service</div></div>
<div class="service abs" style="left:342px;top:1101px"><div class="photo" role="img" aria-label="Hands typing on a laptop keyboard" style="background:linear-gradient(160deg,#6a6a6a,#222)"></div><div class="cap">Copilot /<br>AI Agents</div></div>
<div class="service abs" style="left:610px;top:1101px"><div class="photo" role="img" aria-label="Hand touching a glowing data stream" style="background:linear-gradient(160deg,#c9c9c9,#3a3f46)"></div><div class="cap">Real-time Data Stream Processing</div></div>
<div class="service abs" style="left:877px;top:1101px;background:#000"><div class="photo" style="display:flex;align-items:center;justify-content:center;padding-bottom:70px;color:#fff;font-size:38px;font-weight:600">glidely</div><div class="cap" style="font-size:13px">Customintegration for small to medium business</div></div>

<section class="about abs">
  <div class="kicker2 abs">Who We Are</div>
  <h2 class="display abs">About Us</h2>
  <p class="abs">Our journey began with a focus on Integration Architecture, quickly moving into delivering bespoke systems integration using Halvorsen technologies like FlowLink, CoreNet, DataVault, and CommsKit. Our commitment to excellence quickly earned us recognition, and in 2014, we became a proud Halvorsen Gold Partner, achieving this accolade with the creation of our first 100% native Nimbus cloud solution. We have upheld this esteemed partnership ever since.</p>
  <span class="btn abs">View More</span>
  <div class="about-photo abs" role="img" aria-label="Young developer coding at a desktop monitor and laptop"></div>
</section>

<section class="newsletter abs" role="img" aria-label="Blurred code on a screen behind the newsletter signup">
  <h2 class="abs">Australia's Largest health<br>charity implements</h2>
  <div class="sub abs">Register to our newsletter to find out more.</div>
  <div class="field abs">Enter a valid email address</div>
  <div class="submit abs">SUBMIT</div>
</section>

<section class="blog abs">
  <div class="kicker abs" style="top:50px">News And Press</div>
  <h2 class="sec-title display abs" style="top:68px">Our Blog</h2>

  <article class="post abs" style="left:100px;top:182px;width:318px;height:456px">
    <div class="thumb" role="img" aria-label="Rows of server racks in a data centre" style="height:218px;background:linear-gradient(160deg,#2d5b3c,#0c1a12)"></div>
    <div class="body">
      <div class="date">June 24, 2024</div>
      <h3>Why most upgrade paths for FlowLink lead to using Nimbus Logic apps</h3>
      <p>Introduction In today's fast-evolving technological landscape, businesses are increasingly seeking r...</p>
      <span class="btn">Read More</span>
    </div>
  </article>

  <article class="post main abs" style="left:430px;top:159px;width:356px;height:508px">
    <div class="thumb" role="img" aria-label="Glowing monitor with data visualisations on a desk" style="height:244px;background:linear-gradient(160deg,#6f8a93,#8a7440 70%,#3a3420)"></div>
    <div class="body">
      <div class="date">June 14, 2024</div>
      <h3>How to get visibility into your FlowLink environment</h3>
      <p>In today's fast-paced business environment, the ability to monitor and understand the flow of data within an organisation is crucial ...</p>
      <span class="btn">Read More</span>
    </div>
  </article>

  <article class="post abs" style="left:796px;top:182px;width:319px;height:456px">
    <div class="thumb" role="img" aria-label="Monitor displaying a security vulnerability report" style="height:218px;background:linear-gradient(160deg,#dfe1e3,#9aa0a6)"></div>
    <div class="body">
      <div class="date">June 12, 2024</div>
      <h3>Top 10 FlowLink Server Vulnerabilities and Security Recommendations</h3>
      <p>FlowLink Server is coming to the end of it's life, but is still a critical component for a lot of ent...</p>
      <span class="btn">Read More</span>
    </div>
  </article>

  <span class="btn more abs">View More</span>
</section>

<div class="client abs" style="left:172px;font-size:40px">KTS</div>
<div class="client abs" style="left:399px">Halvorsen</div>
<div class="client abs" style="left:628px">Trackwell</div>
<div class="client abs" style="left:857px">Brightfund</div>

<div class="kicker abs" style="top:3500px">Get In Touch With</div>
<h2 class="sec-title display abs" style="top:3518px">Contact Us</h2>
<div class="contact-lead abs">For more information,Please fill out the following and we will be in touch shortly</div>

<div class="input abs" style="left:102px;top:3655px;width:217px;height:52px">Name</div>
<div class="input abs" style="left:342px;top:3655px;width:216px;height:52px">Mail Id</div>
<div class="input abs" style="left:102px;top:3735px;width:217px;height:52px">Phone</div>
<div class="input abs" style="left:342px;top:3735px;width:216px;height:52px">Subject</div>
<div class="input abs" style="left:102px;top:3810px;width:460px;height:100px">Message</div>
<span class="btn contact-submit abs">Submit</span>
<div class="map abs" role="img" aria-label="Street map of the Melbourne office location"></div>

<footer class="footer abs">
  <div class="brand abs"><span class="brand-mark"></span><span>corvandel</span></div>
  <span class="social abs" style="left:180px" role="img" aria-label="Social profile"></span>
  <span class="social abs" style="left:229px" role="img" aria-label="Social profile"></span>
  <span class="social abs" style="left:277px" role="img" aria-label="Social profile"></span>

  <h4 class="abs" style="left:506px;top:120px">LINKS</h4>
  <ul class="links abs"><li>About Us</li><li>Services Us</li><li>Blog</li><li>Contact Us</li></ul>

  <h4 class="abs" style="left:812px;top:120px">CONTACT US</h4>
  <div class="contact-row abs" style="left:812px;top:174px">
    <span class="icon-circle"><svg width="18" height="18" viewBox="0 0 24 24" fill="#1d5fa8"><path d="M12 2a7 7 0 00-7 7c0 5 7 13 7 13s7-8 7-13a7 7 0 00-7-7zm0 9.5A2.5 2.5 0 1112 6.5a2.5 2.5 0 010 5z"/></svg></span>
    <span>Suite 210, 48 Harbour Lane<br>Melbourne, VIC , 3006</span>
  </div>
  <div class="contact-row abs" style="left:812px;top:240px">
    <span class="icon-circle"><svg width="18" height="18" viewBox="0 0 24 24" fill="#1d5fa8"><path d="M6.6 10.8a15 15 0 006.6 6.6l2.2-2.2c.3-.3.7-.4 1-.2 1.1.4 2.3.6 3.6.6.6 0 1 .4 1 1V20c0 .6-.4 1-1 1A17 17 0 013 4c0-.6.4-1 1-1h3.5c.6 0 1 .4 1 1 0 1.3.2 2.5.6 3.6.1.3 0 .7-.2 1z"/></svg></span>
    <span>1800 555 019</span>
  </div>
  <div class="contact-row abs" style="left:812px;top:292px">
    <span class="icon-circle"><svg width="18" height="18" viewBox="0 0 24 24" fill="none" stroke="#1d5fa8" stroke-width="2"><rect x="3" y="5" width="18" height="14" rx="1"/><path d="M3 6l9 7 9-7"/></svg></span>
    <span>info@corvandel.com</span>
  </div>

  <div class="rule abs"></div>
  <div class="copy abs">© 2025 Company Name, Inc. All Rights Reserved.</div>
</footer>

</body>
</html>
```